Website Banner

I need a website banner for my webpage
Size 950 pixels wide x 284 high
Name of Business: Hattie's Ledgers
Bookkeeping, Registered BAS Agent and KELV Certified consultant.
I would like to use the color purple and Aqua - please refer to the KELV website for ideas. I would like my phone number to be on the banner is possible
0498715263
I have attached a few photos that could be used
Reason: Thanks for the great designs so far - would like to extend for a few more days to see what else comes through.

```html
<!DOCTYPE html>
<html lang="en">
<head>
<meta charset="utf-8">
<title>Hattie's Ledgers – Banner</title>
<link rel="stylesheet" href="https://fonts.googleapis.com/css2?family=Ubuntu:wght@400;500&display=swap">
<style>
  :root {
    --purple-deep: #4e2470;
    --purple-mid: #6f3d93;
    --purple-glow: #a57cc0;
    --purple-text: #55276f;
    --aqua: #14e6ea;
    --aqua-light: #c9ffff;
    --white: #ffffff;
    --rule: #2b1c3a;
  }
  html, body {
    margin: 0;
    padding: 0;
    overflow: hidden;
  }
  body {
    width: 1200px;
    height: 359px;
    font-family: "Ubuntu", "Trebuchet MS", sans-serif;
  }
  .banner {
    position: relative;
    width: 1200px;
    height: 359px;
    overflow: hidden;
    background: radial-gradient(ellipse 520px 300px at 640px 170px, var(--aqua-light) 0%, #7ff6f8 35%, var(--aqua) 75%, #10dde2 100%);
  }
  .top-bar {
    position: absolute;
    inset: 0 0 auto 0;
    height: 46px;
    background: linear-gradient(90deg, var(--purple-deep) 0%, var(--purple-mid) 30%, var(--purple-glow) 52%, var(--purple-mid) 72%, var(--purple-deep) 100%);
    color: var(--white);
    font-size: 33px;
    font-weight: 500;
    line-height: 46px;
    text-shadow: 1px 2px 3px rgba(0, 0, 0, 0.55);
  }
  .business-name {
    position: absolute;
    left: 52px;
    top: 0;
  }
  .phone {
    position: absolute;
    right: 52px;
    top: 0;
    letter-spacing: 0.5px;
  }
  .award-photo {
    position: absolute;
    left: 47px;
    top: 69px;
    width: 214px;
    height: 262px;
    box-sizing: border-box;
    border: 7px solid var(--white);
    border-radius: 14px;
    background: radial-gradient(ellipse at 50% 45%, #c7cfd8 0%, #6b6f7e 30%, #2c2436 65%, #4a3a8c 100%);
  }
  .service {
    position: absolute;
    margin: 0;
    font-size: 38px;
    font-weight: 400;
    color: var(--purple-text);
    text-shadow: 0 0 4px var(--white), 1px 1px 2px var(--white);
    white-space: nowrap;
  }
  .service--bookkeeping { left: 380px; top: 97px; }
  .service--bas { left: 531px; top: 173px; }
  .service--certified { left: 638px; top: 250px; }
  .bottom-rule {
    position: absolute;
    left: 0;
    right: 0;
    bottom: 2px;
    height: 2px;
    background: var(--rule);
  }
</style>
</head>
<body>
  <header class="banner">
    <div class="top-bar">
      <span class="business-name">Hattie's Ledgers</span>
      <span class="phone">Tel: 0498715263</span>
    </div>
    <div class="award-photo" role="img" aria-label="Photograph of a glass consultant award trophy on a stage"></div>
    <p class="service service--bookkeeping">Bookkeeping</p>
    <p class="service service--bas">Registered BAS Agent</p>
    <p class="service service--certified">KELV Certified Consultant</p>
    <div class="bottom-rule"></div>
  </header>
</body>
</html>
```